Packaging design for a reclosable bag for our product

We have a logo, and we need to put it on packaging for our product and while we want the look to be simple, we want it to follow good design principles and also contain spaces for other product descriptions.

There will be 5 sizes at launch so I'd like 5 variations, one for each size.

I've included a few mockups of the type of bag that I made but they are all just rough ideas that I had.

I want the brand to look scientific and methodical and even a bit quirky, as in "wow this is a serious product but also a bit unusual."

```html
<!DOCTYPE html>
<html lang="en">
<head>
<meta charset="utf-8">
<title>NV4 Bias Lighting Pouch</title>
<link href="https://fonts.googleapis.com/css2?family=Open+Sans:wght@300;700&display=swap" rel="stylesheet">
<style>
  :root {
    --page-bg: #ffffff;
    --pouch-dark: #0c0c0c;
    --pouch-light: #f3f3f3;
    --ink-light: #e8e8e8;
    --ink-dark: #0a0a0a;
    --edge-light: #dcdcdc;
  }
  html, body {
    margin: 0;
    padding: 0;
    overflow: hidden;
  }
  body {
    width: 1200px;
    height: 1040px;
    background: var(--page-bg);
    position: relative;
    font-family: "Open Sans", Arial, sans-serif;
  }
  .pouch {
    position: absolute;
    top: 75px;
    width: 458px;
    height: 650px;
    border-radius: 14px 14px 2px 2px;
    box-sizing: border-box;
  }
  .pouch--dark {
    left: 148px;
    background: var(--pouch-dark);
    color: var(--ink-light);
  }
  .pouch--light {
    left: 648px;
    background: var(--pouch-light);
    border: 1px solid var(--edge-light);
    color: var(--ink-dark);
  }
  .pouch__seal {
    position: absolute;
    left: 0;
    right: 0;
    top: 62px;
    height: 1px;
    background: currentColor;
    opacity: 0.06;
  }
  .brand-name {
    position: absolute;
    left: 30px;
    top: 118px;
    margin: 0;
    font-weight: 300;
    font-size: 232px;
    line-height: 1;
    letter-spacing: -6px;
  }
  .spec {
    position: absolute;
    left: 250px;
    top: 540px;
    display: flex;
    align-items: flex-start;
    gap: 20px;
  }
  .spec__size {
    display: flex;
    flex-direction: column;
    align-items: center;
    margin-left: -128px;
    width: 108px;
  }
  .spec__number {
    font-weight: 700;
    font-size: 68px;
    line-height: 0.9;
  }
  .spec__unit {
    font-weight: 300;
    font-size: 18px;
    line-height: 1.1;
  }
  .spec__details {
    margin: 0;
    padding: 0;
    list-style: none;
    font-weight: 300;
    font-size: 15.5px;
    line-height: 20px;
  }
</style>
</head>
<body>
  <section class="pouch pouch--dark">
    <div class="pouch__seal"></div>
    <h1 class="brand-name">NV4</h1>
    <div class="spec">
      <div class="spec__size">
        <span class="spec__number">5</span>
        <span class="spec__unit">meters</span>
      </div>
      <ul class="spec__details">
        <li>Extra Large</li>
        <li>Bias Lighting</li>
        <li>Simulated D65 CRI 90+</li>
        <li>6500K White</li>
      </ul>
    </div>
  </section>

  <section class="pouch pouch--light">
    <div class="pouch__seal"></div>
    <h1 class="brand-name">NV4</h1>
    <div class="spec">
      <div class="spec__size">
        <span class="spec__number">5</span>
        <span class="spec__unit">meters</span>
      </div>
      <ul class="spec__details">
        <li>Extra Large</li>
        <li>Bias Lighting</li>
        <li>Simulated D65 CRI 90+</li>
        <li>6500K White</li>
      </ul>
    </div>
  </section>
</body>
</html>
```